Roofing Contractor business card redesign

I want to redesign my business card with a fresh, eye catching concept

Target Market(s)

Residential Roofing Clients, potential employees, and subcontractors.

Industry/Entity Type

Business

Colors

Designer to choose colors to be used in the design.

Requirements
Nice to have
• I just want something that's more pleasing to the eye. You can use a combination of either / or of my logos.

```html
<!DOCTYPE html>
<html lang="en">
<head>
<meta charset="utf-8">
<title>Fair Hand Builders – Business Card</title>
<link href="https://fonts.googleapis.com/css2?family=Oswald:wght@500&family=Work+Sans:wght@300;500&display=swap" rel="stylesheet">
<style>
  :root {
    --orange: #f38221;
    --brown: #4a1710;
    --ink: #2b2b2b;
    --paper: #ffffff;
    --backdrop: #2a2a2a;
  }
  html, body { margin: 0; padding: 0; overflow: hidden; }
  body { width: 1200px; height: 930px; background: var(--backdrop); position: relative; font-family: 'Work Sans', sans-serif; }
  .card { position: absolute; width: 646px; height: 368px; border-radius: 26px; overflow: hidden; }
  .card-front { left: 277px; top: 76px; background: var(--paper); }
  .card-back { left: 277px; top: 486px; background: var(--orange); }

  .person-name { position: absolute; left: 39px; top: 160px; margin: 0; font-family: 'Oswald', sans-serif; font-weight: 500; font-size: 30px; letter-spacing: 0.5px; color: var(--orange); line-height: 1; }
  .person-roles { position: absolute; left: 39px; top: 199px; margin: 0; font-weight: 300; font-size: 16.5px; line-height: 20px; color: var(--ink); }
  .divider { position: absolute; left: 39px; top: 247px; width: 567px; height: 1px; background: var(--brown); }
  .contact-list { position: absolute; left: 39px; top: 264px; margin: 0; padding: 0; list-style: none; font-weight: 300; font-size: 16.5px; color: var(--ink); }
  .contact-list li { display: flex; align-items: center; height: 20px; }
  .contact-list svg { width: 12px; height: 12px; margin-right: 12px; flex: none; }
  .address { position: absolute; right: 40px; top: 284px; margin: 0; text-align: right; font-style: normal; font-weight: 300; font-size: 16.5px; line-height: 20px; color: var(--ink); }

  .brand-name { position: absolute; right: 40px; top: 150px; display: flex; align-items: center; gap: 10px; font-weight: 500; font-size: 20px; line-height: 1; color: var(--brown); }
  .brand-name .dot { width: 26px; height: 26px; border-radius: 50%; background: var(--orange); flex: none; }

  .card-wave { position: absolute; left: 0; bottom: 0; width: 646px; height: 40px; }

  .back-name { position: absolute; left: 0; right: 0; top: 160px; display: flex; justify-content: center; align-items: center; gap: 16px; font-weight: 500; font-size: 38px; line-height: 1; color: var(--brown); }
  .back-name .dot { width: 40px; height: 40px; border-radius: 50%; background: var(--brown); flex: none; }
</style>
</head>
<body>
  <section class="card card-front">
    <div class="brand-name"><span class="dot"></span><span>Fair Hand Builders</span></div>

    <h1 class="person-name">DAN HARLOW</h1>
    <p class="person-roles">Keystone Certified Roof Inspector<br>Licensed Property Adjuster</p>
    <div class="divider"></div>

    <ul class="contact-list">
      <li><svg viewBox="0 0 12 12"><path d="M2.5 1 L4.5 1 L5 3.5 L3.8 4.4 Q5 7 7.6 8.2 L8.5 7 L11 7.5 L11 9.5 Q11 11 9.5 11 Q1 10 1 2.5 Q1 1 2.5 1Z" fill="var(--orange)"/></svg>(555) 318-2200</li>
      <li><svg viewBox="0 0 12 12"><rect x="3" y="0.5" width="6" height="11" rx="1" fill="none" stroke="var(--orange)" stroke-width="1.4"/><circle cx="6" cy="9.3" r="0.8" fill="var(--orange)"/></svg>(555) 762-4481</li>
      <li><svg viewBox="0 0 12 12"><rect x="0.8" y="2.5" width="10.4" height="7.5" fill="none" stroke="var(--orange)" stroke-width="1.3"/><path d="M1 3 L6 7 L11 3" fill="none" stroke="var(--orange)" stroke-width="1.3"/></svg>dan@fairhandbuilders.com</li>
    </ul>

    <address class="address">4410 Cedar Hollow Road<br>Suite 118 Ashford, TX 75000</address>

    <svg class="card-wave" viewBox="0 0 646 40" preserveAspectRatio="none" aria-hidden="true">
      <path d="M0 20 L470 20 Q490 20 500 12 Q515 2 535 2 L646 2 L646 40 L0 40 Z" fill="var(--orange)"/>
      <path d="M0 9 L372 9 L360 14 L0 14 Z" fill="var(--brown)"/>
      <path d="M0 14 L360 14 Q370 14 385 9 L470 9 Q455 16 440 20 L0 20 Z" fill="var(--paper)"/>
    </svg>
  </section>

  <section class="card card-back">
    <div class="back-name"><span class="dot"></span><span>Fair Hand Builders, Inc.</span></div>
  </section>
</body>
</html>
```